Vibrant, yet professional, stationery set and other designs required.

I need to source a fantastic designer for a new project as part of my company using a new logo designed via sketch harbor.

**UPDATE** I am not looking for just 'fine' design that will suffice. I am looking for something great.

We are a life assurance brokerage based in Dublin, Ireland and BrightRoost.ie is our new website aimed at providing services for young families in Ireland. We are hoping to be the 'Velro' level of service providers in this area and I am looking for the quality of design to reflect this :-) Hopefully that makes sense!

I have a preference for straight lines over curves and waves.

I need...

1. Business card
2. Letterhead
3. Banner (for printing - 76cm X 305cm)
4. Car branding for KORVA 9 (2014 sport model) I believe the templates are freely available online.

Target Market(s)

Parents in Ireland - Aged 27 to 50.

Industry/Entity Type

Financial Planning

Colors

Designer to choose colors to be used in the design.

Requirements
Must have
• All of the items listed in the description above. I like clean, bright, legible, vibrant and professional design.
Should not have
• No silly or 'cheap' looking designs. This is a professional company looking to provide a professional service.

```html
<!DOCTYPE html>
<html lang="en">
<head>
<meta charset="UTF-8">
<title>BrightRoost.ie – Business Card</title>
<link rel="stylesheet" href="https://fonts.googleapis.com/css2?family=Roboto:wght@400;500;700&display=swap">
<style>
  :root {
    --backdrop: #b9b9b9;
    --orange: #ef8019;
    --green: #9bc53d;
    --blue: #6ccbe8;
    --slate: #8d999e;
    --ink: #555a5e;
    --paper: #f4f4f2;
    --white: #ffffff;
  }
  * { margin: 0; padding: 0; box-sizing: border-box; }
  html, body { width: 1200px; height: 960px; overflow: hidden; }
  body {
    background: var(--backdrop);
    font-family: "Roboto", Arial, sans-serif;
    position: relative;
  }
  .card { position: absolute; width: 600px; height: 342px; }

  /* Front */
  .card-front { left: 320px; top: 104px; background: var(--orange); }
  .card-front .brand {
    position: absolute; left: 0; right: 0; top: 128px;
    text-align: center; color: var(--white);
    font-weight: 500; font-size: 54px; letter-spacing: -0.5px;
  }
  .card-front .web {
    position: absolute; left: 0; right: 0; top: 290px;
    text-align: center; color: var(--white);
    font-size: 14px; letter-spacing: 6px;
  }

  /* Back */
  .card-back { left: 320px; top: 493px; background: var(--paper); }
  .accent-bar { position: absolute; left: 0; width: 12px; }
  .accent-green { top: 73px; height: 65px; background: var(--green); }
  .accent-orange { top: 140px; height: 64px; background: var(--orange); }
  .accent-blue { top: 206px; height: 64px; background: var(--blue); }
  .edge-bar { position: absolute; right: 0; top: 73px; width: 15px; height: 197px; background: var(--slate); }

  .contact { position: absolute; left: 29px; top: 76px; color: var(--ink); }
  .contact .name { color: var(--orange); font-weight: 700; font-size: 19px; line-height: 22px; }
  .contact .role { color: var(--slate); font-weight: 500; font-size: 14px; margin-top: 4px; }
  .contact .address { font-size: 14px; line-height: 18px; margin-top: 9px; }
  .contact .lines { list-style: none; margin-top: 10px; font-size: 14px; }
  .contact .lines li { display: flex; align-items: center; height: 19px; }
  .contact .lines svg { width: 14px; height: 14px; margin-right: 9px; fill: var(--orange); }

  .card-back .brand {
    position: absolute; left: 330px; width: 250px; top: 152px;
    text-align: center; color: var(--slate);
    font-weight: 500; font-size: 38px; letter-spacing: -0.3px;
  }
</style>
</head>
<body>

<section class="card card-front">
  <div class="brand">BrightRoost.ie</div>
  <div class="web">www.brightroost.ie</div>
</section>

<section class="card card-back">
  <span class="accent-bar accent-green"></span>
  <span class="accent-bar accent-orange"></span>
  <span class="accent-bar accent-blue"></span>
  <span class="edge-bar"></span>

  <div class="contact">
    <div class="name">CIARAN DOYLE</div>
    <div class="role">CEO/FOUNDER</div>
    <div class="address">14 Larkfield Row<br>Ranelagh, Dublin 6</div>
    <ul class="lines">
      <li><svg viewBox="0 0 16 16" aria-hidden="true"><path d="M3.5 1l3 3-1.6 1.8c.9 2 2.4 3.5 4.3 4.3L11 8.5l3 3-1.8 2.5C6.5 14 2 9.5 2 3.8z"/></svg>01 482 5170</li>
      <li><svg viewBox="0 0 16 16" aria-hidden="true"><path d="M4.5 1h7v14h-7zM6 3v8.5h4V3zm2 9.5a.8.8 0 100 1.6.8.8 0 000-1.6z" fill-rule="evenodd"/></svg>087 631 2294</li>
      <li><svg viewBox="0 0 16 16" aria-hidden="true"><path d="M4 1h8v4H4zM1 6h14v6h-2v3H3v-3H1zm4 4v3h6v-3z" fill-rule="evenodd"/></svg>01 482 5171</li>
      <li><svg viewBox="0 0 16 16" aria-hidden="true"><path d="M1 3.5h14v9H1zm1.5 1.2L8 9l5.5-4.3z" fill-rule="evenodd"/></svg>hello@brightroost.ie</li>
      <li><svg viewBox="0 0 16 16" aria-hidden="true"><path d="M8 1a7 7 0 110 14A7 7 0 018 1zm-3 3.5L6.5 7 5 9.5l2 1V13l2-2 1-2.5-2-1.5 1-2.5z" fill-rule="evenodd"/></svg>www.brightroost.ie</li>
    </ul>
  </div>

  <div class="brand">BrightRoost.ie</div>
</section>

</body>
</html>
```